business card deign

Logo needs the following on it.
1. attached logo
2. Tagline - "If it keeps the ice frosty or the music loud...we bring it!"
3. Name- Dalton Pikes, Founder and CPO
4. Address - 412 E. Carver Avenue, Ste 2207, Tampa, FL. 33917
5. Phone - 555.318.4726

```html
<!DOCTYPE html>
<html lang="en">
<head>
<meta charset="utf-8">
<title>Brisley Business Card</title>
<link rel="stylesheet" href="https://fonts.googleapis.com/css2?family=Open+Sans:wght@400;600;700;800&display=swap">
<style>
  :root {
    --backdrop: #222222;
    --gold-dark: #8e6233;
    --gold-mid: #c29a5c;
    --gold-light: #fbe9a8;
    --gold-deep: #ad7a36;
    --ink: #0d0b08;
    --embossed: #8a5d2c;
    --band: #050403;
    --tagline: #c9a25e;
  }
  * { margin: 0; padding: 0; box-sizing: border-box; }
  html, body {
    width: 1200px;
    height: 711px;
    overflow: hidden;
    background: var(--backdrop);
    font-family: "Open Sans", Arial, sans-serif;
  }
  .canvas {
    position: relative;
    width: 1200px;
    height: 711px;
  }
  .card {
    position: absolute;
    top: 201px;
    width: 540px;
    height: 309px;
    border-radius: 22px;
    overflow: hidden;
    background: linear-gradient(115deg,
      var(--gold-dark) 0%,
      var(--gold-mid) 30%,
      var(--gold-light) 50%,
      var(--gold-mid) 72%,
      var(--gold-deep) 100%);
    box-shadow: 0 14px 28px rgba(0,0,0,0.6);
  }
  .card--front { left: 40px; }
  .card--back { left: 620px; }

  .brand-name {
    font-weight: 800;
    color: var(--ink);
    letter-spacing: 0.32em;
    text-transform: uppercase;
    white-space: nowrap;
  }
  .card--front .brand {
    position: absolute;
    inset: 0;
    display: flex;
    align-items: center;
    justify-content: center;
  }
  .card--front .brand-name {
    font-size: 52px;
    color: var(--embossed);
    padding-left: 0.32em;
  }

  .card--back .brand {
    position: absolute;
    left: 0;
    top: 0;
    width: 270px;
    height: 262px;
    display: flex;
    align-items: center;
    justify-content: center;
  }
  .card--back .brand-name {
    font-size: 30px;
    padding-left: 0.32em;
  }
  .divider {
    position: absolute;
    left: 270px;
    top: 42px;
    width: 1px;
    height: 190px;
    background: rgba(20,14,6,0.75);
  }
  .contact {
    position: absolute;
    left: 296px;
    top: 62px;
    color: var(--ink);
  }
  .contact__name {
    font-size: 24px;
    font-weight: 800;
    line-height: 1.1;
  }
  .contact__role {
    font-size: 13px;
    font-weight: 700;
    margin-top: 2px;
  }
  .contact__list {
    list-style: none;
    margin-top: 16px;
    font-size: 12.5px;
    line-height: 1.35;
  }
  .contact__item {
    display: flex;
    align-items: flex-start;
    gap: 7px;
    margin-bottom: 3px;
  }
  .contact__icon {
    flex: none;
    width: 12px;
    height: 12px;
    margin-top: 2px;
  }
  .tagline-band {
    position: absolute;
    left: 0;
    right: 0;
    bottom: 20px;
    height: 28px;
    background: var(--band);
    display: flex;
    align-items: center;
    padding-left: 26px;
  }
  .tagline {
    color: var(--tagline);
    font-size: 14px;
    font-weight: 600;
    letter-spacing: 0.01em;
    white-space: nowrap;
  }
</style>
</head>
<body>
<main class="canvas">
  <section class="card card--front" aria-label="Card front">
    <div class="brand">
      <span class="brand-name">Brisley</span>
    </div>
  </section>

  <section class="card card--back" aria-label="Card back">
    <div class="brand">
      <span class="brand-name">Brisley</span>
    </div>
    <div class="divider"></div>
    <div class="contact">
      <p class="contact__name">Dalton Pikes</p>
      <p class="contact__role">Founder and CPO</p>
      <ul class="contact__list">
        <li class="contact__item">
          <svg class="contact__icon" viewBox="0 0 24 24" aria-hidden="true">
            <path fill="#0d0b08" d="M6.6 10.8a15.1 15.1 0 0 0 6.6 6.6l2.2-2.2a1 1 0 0 1 1-.25 11.4 11.4 0 0 0 3.6.57 1 1 0 0 1 1 1V20a1 1 0 0 1-1 1A17 17 0 0 1 3 4a1 1 0 0 1 1-1h3.5a1 1 0 0 1 1 1c0 1.250.2 2.45.57 3.57a1 1 0 0 1-.25 1z"/>
          </svg>
          <span>555.318.4726</span>
        </li>
        <li class="contact__item">
          <svg class="contact__icon" viewBox="0 0 24 24" aria-hidden="true">
            <path fill="#0d0b08" d="M12 2a7 7 0 0 0-7 7c0 5.2 7 13 7 13s7-7.8 7-13a7 7 0 0 0-7-7zm0 9.5A2.5 2.5 0 1 1 12 6.5a2.5 2.5 0 0 1 0 5z"/>
          </svg>
          <span>412 E. Carver Avenue,<br>Ste 2207, Tampa, FL. 33917</span>
        </li>
      </ul>
    </div>
    <div class="tagline-band">
      <p class="tagline">If it keeps the ice frosty or the music loud...we bring it!</p>
    </div>
  </section>
</main>
</body>
</html>
```